Elevate our existing website to be more luxury and add your pizazz!

We are seeking someone to bring some freshness to our recently redesigned website. I feel like it is missing some of the luxury, high end and rustic feelings we wanted from it. It is missing some pizazz! My goal was to have an intuitive, immersive, and captivating high-end website that resonates with my handmade art. I wanted a blend of creativity, rustic charm, luxury and high-end functionality, ensuring an easy-to-use and secure browsing experience that speaks to our brand of hand made and crafted items.
Design Aesthetics:
I love immersive nature. I'd love to feel like my website was a walk in the forest, the flowers, etc. Leaving the visitor feeling refreshed and inspired.
The design should seamlessly merge rustic elements with modern inspiration, evoking a sense of being surrounded by nature.
We're drawn to a moody ambiance that captures the essence of a forest, without veering into darkness.
While avoiding the typical all-white background, we aim for a balanced and visually appealing color scheme with perhaps elements floating into the frame with artful taste.
The site was designed in Elementor and I can provide you with the Wordpress login to make the changes once approved.
Branding Guide: https://www.plinthbox.com/design/QRmZtPeLqWs/VnTy82KdRoEuJxCbMa4wGp/watch?utm_content=QRmZtPeLqWs&utm_campaign=designshare&utm_medium=link&utm_source=publishsharelink
Recently redesigned website: dev.mossrivertwine.com
Target Market(s)
Luxury Crafters , Knitters and Crocheters
Industry/Entity Type
Art
Number of Pages Required
1 page

```html
<!DOCTYPE html>
<html lang="en">
<head>
<meta charset="utf-8">
<title>Moss River Twine</title>
<link rel="stylesheet" href="https://fonts.googleapis.com/css2?family=Prata&family=Josefin+Sans:wght@300;400;600&family=Mrs+Saint+Delafield&display=swap">
<style>
:root{
  --forest:#2f3d32;
  --forest-deep:#34443a;
  --mint:#dce6da;
  --ink:#1f231f;
  --muted:#4a4f4a;
  --bark:#2a1f19;
  --heart:#d0142c;
  --star:#f2b705;
  --ornament:#c9d2c7;
  --white:#ffffff;
}
*{margin:0;padding:0;box-sizing:border-box}
html,body{width:1200px;height:4812px;overflow:hidden}
body{position:relative;background:var(--white);font-family:"Josefin Sans",sans-serif;color:var(--ink)}
.abs{position:absolute}
.photo{position:absolute;display:block}
.serif{font-family:"Prata",serif;font-weight:400}
.script{font-family:"Mrs Saint Delafield",cursive;font-weight:400}
.btn{position:absolute;display:flex;align-items:center;justify-content:center;gap:6px;background:var(--forest);color:var(--white);border-radius:20px;font-size:12px;letter-spacing:.5px;text-decoration:none}
.btn svg{width:11px;height:11px}
.eyebrow{display:flex;align-items:center;gap:8px;font-size:40px;color:var(--ink);white-space:nowrap}
.eyebrow .rule{height:1px;background:var(--ink)}
.eyebrow .ornament{width:40px;height:26px;background:var(--ornament)}

/* header */
.site-header{position:absolute;top:0;left:0;width:1200px;height:97px;background:var(--white)}
.brand{position:absolute;left:121px;top:24px;display:flex;align-items:center;gap:10px}
.brand-name{font-family:"Prata",serif;font-size:22px;color:var(--ink)}
.brand-dot{width:44px;height:44px;border-radius:50%;background:var(--forest)}
.main-nav{position:absolute;left:445px;top:36px;display:flex;gap:24px;font-size:14px}
.main-nav a{color:var(--ink);text-decoration:none}
.header-icons{position:absolute;left:980px;top:36px;display:flex;gap:12px}
.header-icons svg{width:16px;height:16px}

/* hero */
.hero{position:absolute;top:97px;left:0;width:1200px;height:663px;background:linear-gradient(160deg,#f2f3f1 0%,#e4e8e2 55%,#d3d9d0 100%)}
.hero h1{position:absolute;left:471px;top:120px;font-size:52px;line-height:62px;letter-spacing:2px}
.hero .made{position:absolute;left:471px;top:60px;font-size:50px}
.hero p{position:absolute;left:471px;top:249px;width:340px;font-size:11.5px;line-height:19px;letter-spacing:.4px}

/* intro */
.intro .title{position:absolute;left:635px;top:893px;font-size:38px;line-height:50px;letter-spacing:1px}
.intro .caps{position:absolute;left:637px;top:1009px;width:430px;font-size:10.5px;line-height:23px;letter-spacing:.6px;text-transform:uppercase}
.intro .body{position:absolute;left:637px;top:1081px;width:440px;font-size:10px;line-height:24.5px;letter-spacing:.3px}

/* wood band */
.wood{position:absolute;top:1380px;left:0;width:1200px;height:400px;background:var(--mint)}
.wood h2{position:absolute;left:290px;width:636px;top:86px;text-align:center;font-size:40px;letter-spacing:2px}
.wood p{position:absolute;left:305px;width:606px;top:162px;text-align:center;font-size:11.5px;line-height:27.5px;letter-spacing:.6px}

/* products */
.products h2{position:absolute;left:0;width:1200px;top:1905px;text-align:center;font-size:38px}
.card{position:absolute;top:1994px;width:281px;height:380px;background:var(--white);box-shadow:0 2px 8px rgba(0,0,0,.18)}
.card .thumb{position:absolute;left:14px;top:19px;width:250px;height:206px;background:var(--mint)}
.card h3{position:absolute;left:14px;top:249px;font-family:"Prata",serif;font-weight:400;font-size:15px;letter-spacing:.8px;white-space:nowrap}
.card .price{position:absolute;left:14px;top:282px;font-size:14px;font-weight:600}
.card .rate{position:absolute;left:156px;top:281px;display:flex;gap:10px;align-items:center}
.card .btn{left:14px;top:318px;width:120px;height:32px;font-size:10px}
.slider-arrow{position:absolute;top:2160px;width:26px;height:26px;border-radius:50%;background:#c8cbc8;display:flex;align-items:center;justify-content:center}

/* explore */
.explore{position:absolute;top:2462px;left:0;width:598px;height:472px;background:var(--mint)}
.explore h2{position:absolute;left:110px;top:55px;font-size:40px;line-height:52px;letter-spacing:2.5px}
.explore p{position:absolute;left:110px;top:174px;width:450px;font-size:11px;line-height:24px;letter-spacing:.4px}

/* seen in */
.seen h2{position:absolute;left:0;width:1200px;top:3008px;text-align:center;font-size:40px;letter-spacing:2px}
.badge{position:absolute;top:3120px;width:130px;height:76px;background:#eceeed;border-radius:6px}

/* banner */
.banner{position:absolute;top:3308px;left:0;width:1200px;height:267px;background:linear-gradient(90deg,#e3e6e0,#d8dcd3 30%,#e6e2d8 60%,#dde2db)}
.banner .plate{position:absolute;left:299px;top:103px;width:570px;height:90px;background:rgba(52,68,58,.82);display:flex;align-items:center;justify-content:center;color:var(--white);font-family:"Prata",serif;font-size:40px;letter-spacing:3px}

/* follow */
.follow h2{position:absolute;left:0;width:1200px;top:3705px;text-align:center;font-size:40px;letter-spacing:2px}

/* footer */
.site-footer{position:absolute;top:4426px;left:0;width:1200px;height:386px;background:var(--forest-deep);color:var(--white)}
.site-footer .f-brand{position:absolute;left:112px;top:55px;font-family:"Prata",serif;font-size:26px}
.site-footer .f-dot{position:absolute;left:385px;top:40px;width:58px;height:58px;border-radius:50%;background:var(--white)}
.site-footer .news{position:absolute;left:120px;top:152px;font-family:"Prata",serif;font-size:16px;letter-spacing:1.5px}
.site-footer .field{position:absolute;left:112px;top:196px;width:322px;height:45px;background:var(--white);border-radius:23px;color:#333;font-size:12px;padding:16px 26px;letter-spacing:.5px}
.site-footer .sub{position:absolute;left:112px;top:260px;width:123px;height:37px;background:var(--bark);border-radius:19px;display:flex;align-items:center;justify-content:center;font-size:12px;letter-spacing:.5px}
.f-col{position:absolute;top:70px}
.f-col h4{font-family:"Prata",serif;font-weight:400;font-size:18px;letter-spacing:1.5px;margin-bottom:18px}
.f-col a{display:flex;align-items:center;gap:12px;color:var(--white);text-decoration:none;font-size:11.5px;letter-spacing:1px;height:27.5px}
.f-col .sq{width:11px;height:11px;border:1.5px solid var(--white);border-radius:2px}
.site-footer .line{position:absolute;left:112px;top:350px;width:976px;height:1px;background:rgba(255,255,255,.6)}
.site-footer .copy{position:absolute;left:0;width:1200px;top:366px;text-align:center;font-size:11px;letter-spacing:1px}
</style>
</head>
<body>

<header class="site-header">
  <div class="brand">
    <span class="brand-name">mossrivertwine</span>
    <span class="brand-dot"></span>
  </div>
  <nav class="main-nav">
    <a href="#">Home</a><a href="#">About Us</a><a href="#">Shop</a><a href="#">Custom Order</a><a href="#">Feedback</a><a href="#">Contact</a>
  </nav>
  <div class="header-icons">
    <svg viewBox="0 0 16 16"><path d="M8 14L2 8a3.3 3.3 0 015-4.3L8 5l1-1.3A3.3 3.3 0 0114 8z" fill="var(--forest)"/></svg>
    <svg viewBox="0 0 16 16"><path d="M1 2h3l2 8h8l2-6H5" fill="none" stroke="var(--forest)" stroke-width="1.8"/><circle cx="7" cy="13" r="1.4" fill="var(--forest)"/><circle cx="13" cy="13" r="1.4" fill="var(--forest)"/></svg>
    <svg viewBox="0 0 16 16"><circle cx="8" cy="5" r="3.5" fill="var(--forest)"/><path d="M1.5 16a6.5 6 0 0113 0z" fill="var(--forest)"/></svg>
    <svg viewBox="0 0 16 16"><circle cx="6.5" cy="6.5" r="5" fill="none" stroke="var(--forest)" stroke-width="1.8"/><path d="M10 10l5 5" stroke="var(--forest)" stroke-width="2"/></svg>
  </div>
</header>

<section class="hero">
  <div class="photo" role="img" aria-label="Necklace with a carved wooden pendant worn over a patterned top" style="left:58px;top:0;width:263px;height:314px;border-radius:0 0 132px 132px;background:linear-gradient(180deg,#c9a48e,#b86c62 60%,#e5c2b8)"></div>
  <div class="photo" role="img" aria-label="Carved wooden hair pin in dark hair" style="left:260px;top:368px;width:176px;height:255px;border-radius:88px;background:linear-gradient(170deg,#6a4f3e,#2c1e18 60%,#8a6a55)"></div>
  <div class="photo" role="img" aria-label="Green leaves drifting into the frame" style="left:1040px;top:0;width:160px;height:70px;background:linear-gradient(135deg,#a8cf84,#6fa34e)"></div>
  <div class="photo" role="img" aria-label="Green leaves drifting into the frame" style="left:0;top:610px;width:120px;height:50px;background:linear-gradient(135deg,#a0c97c,#5f9544)"></div>
  <div class="script made">Made By Hand</div>
  <h1 class="serif">From Nature,<br>Refined</h1>
  <p>Inspired by the beauty and usefulness of wood, I started playing with sticks. This is my process of realizing their potential. I create heirloom crochet hooks and knitting needles: rustic, refined or embellished with hand-painted art.</p>
  <a class="btn" href="#" style="left:471px;top:370px;width:135px;height:38px">Shop Now <svg viewBox="0 0 12 12"><path d="M2 2l4 4-4 4M6 2l4 4-4 4" fill="none" stroke="#fff" stroke-width="1.3"/></svg></a>
  <div class="photo" role="img" aria-label="Carved crochet hooks on dark slate beside undyed yarn" style="left:847px;top:219px;width:353px;height:321px;border-radius:160px 0 0 160px;background:linear-gradient(150deg,#e8dcc5 0%,#3a3c3a 35%,#2a2b2a 70%,#b8915a)"></div>
</section>

<section class="intro">
  <div class="photo" role="img" aria-label="Hand holding carved crochet hooks over autumn leaves" style="left:112px;top:847px;width:320px;height:443px;background:linear-gradient(160deg,#6b5a3d,#3c3221 55%,#8d7450)"></div>
  <div class="photo" role="img" aria-label="Painted hooks resting on an open book with sunflowers" style="left:305px;top:908px;width:256px;height:329px;border:5px solid var(--white);background:linear-gradient(160deg,#d9a730,#3b3224 40%,#c9c4b4 70%,#4a4030)"></div>
  <div class="abs eyebrow" style="left:632px;top:838px">
    <span class="script">Mossrivertwine</span><span class="rule" style="width:90px"></span><span class="ornament" role="img" aria-label="Leaf ornament"></span>
  </div>
  <h2 class="serif title">More Than Just Tools,<br>It's Art For Your Craft.</h2>
  <p class="caps">Inspired by the beauty and usefulness of wood, I started playing with sticks. This is my process of realizing their potential.</p>
  <p class="body">I create heirloom crochet hooks and knitting needles: rustic, refined or embellished with hand-painted art. Each one is unique, and all are hand-carved from the trees that grace our landscape. Choose from live oak, aromatic camphor, cypress, pine and sometimes treats like avocado, basil, or found mystery wood. All cuts are made seasonally during trimming and never harm the tree. From my heart to your hands, our craft.</p>
  <a class="btn" href="#" style="left:637px;top:1256px;width:135px;height:37px">Read More <svg viewBox="0 0 12 12"><path d="M2 2l4 4-4 4M6 2l4 4-4 4" fill="none" stroke="#fff" stroke-width="1.3"/></svg></a>
</section>

<section class="wood">
  <div class="photo" role="img" aria-label="Skeins of hand-dyed yarn with carved hooks" style="left:0;top:0;width:290px;height:400px;background:linear-gradient(150deg,#8a5a3a,#3e5a5a 40%,#6b4a2a 70%,#2a2a2a)"></div>
  <div class="photo" role="img" aria-label="Forest of tall pines above a stack of cut logs" style="left:926px;top:0;width:274px;height:400px;background:linear-gradient(180deg,#3a3a22,#c08a40 35%,#7a4a22 65%,#4a2a16)"></div>
  <div class="abs eyebrow" style="left:410px;top:30px">
    <span class="script">the grainlines go deep</span><span class="rule" style="width:90px"></span><span class="ornament" role="img" aria-label="Leaf ornament"></span>
  </div>
  <h2 class="serif">Inspired By Wood</h2>
  <p>Wood is inspiring. Even fallen branches and sticks continue the life of the tree in their fibers and seem the perfect accompaniment to wool and other fiber work. My hooks are handmade using a variety of wood sources from our natural landscape. Some hooks are perfect in their rustic state, while others are a backdrop for hand-painted works of art. All are unique, one-of-a-kind tools.</p>
  <a class="btn" href="#" style="left:532px;top:323px;width:136px;height:37px">Read More <svg viewBox="0 0 12 12"><path d="M2 2l4 4-4 4M6 2l4 4-4 4" fill="none" stroke="#fff" stroke-width="1.3"/></svg></a>
</section>

<section class="products">
  <div class="abs eyebrow" style="left:425px;top:1855px">
    <span class="script">the grainlines go deep</span><span class="rule" style="width:90px"></span><span class="ornament" role="img" aria-label="Leaf ornament"></span>
  </div>
  <h2 class="serif">Product</h2>
  <div class="slider-arrow" style="left:52px"><svg width="12" height="12" viewBox="0 0 12 12"><path d="M8 2L4 6l4 4" fill="none" stroke="#fff" stroke-width="2"/></svg></div>
  <div class="slider-arrow" style="left:1133px"><svg width="12" height="12" viewBox="0 0 12 12"><path d="M4 2l4 4-4 4" fill="none" stroke="#fff" stroke-width="2"/></svg></div>

  <article class="card" style="left:112px">
    <div class="thumb" role="img" aria-label="Glittering hooks beside a plume" style="background:linear-gradient(135deg,#dce6da 10%,#f4f4f1 25%,#f4f4f1 75%,#dce6da 90%)"></div>
    <h3>Shimmer Plume Hook</h3>
    <div class="price">$55.00</div>
    <div class="rate"><svg width="18" height="16" viewBox="0 0 16 14"><path d="M8 14L1.5 7.5a3.8 3.8 0 016.5-4 3.8 3.8 0 016.5 4z" fill="var(--heart)"/></svg><svg width="58" height="11" viewBox="0 0 60 11" fill="var(--star)"><g id="s"><path d="M5.5 0l1.6 3.5 3.9.3-3 2.5.9 3.8-3.4-2-3.4 2 .9-3.8-3-2.5 3.9-.3z"/></g><use href="#s" x="12"/><use href="#s" x="24"/><use href="#s" x="36"/><use href="#s" x="48"/></svg></div>
    <a class="btn" href="#">Add To Cart <svg viewBox="0 0 12 12"><path d="M2 2l4 4-4 4M6 2l4 4-4 4" fill="none" stroke="#fff" stroke-width="1.3"/></svg></a>
  </article>
  <article class="card" style="left:458px">
    <div class="thumb" role="img" aria-label="Carved hook beside a pot of lilac" style="background:linear-gradient(135deg,#dce6da 10%,#f4f4f1 25%,#f4f4f1 75%,#dce6da 90%)"></div>
    <h3>Lilac Sprig Hook, made to order</h3>
    <div class="price">$155.00</div>
    <div class="rate"><svg width="18" height="16" viewBox="0 0 16 14"><path d="M8 14L1.5 7.5a3.8 3.8 0 016.5-4 3.8 3.8 0 016.5 4z" fill="var(--heart)"/></svg><svg width="58" height="11" viewBox="0 0 60 11" fill="var(--star)"><use href="#s"/><use href="#s" x="12"/><use href="#s" x="24"/><use href="#s" x="36"/><use href="#s" x="48"/></svg></div>
    <a class="btn" href="#">Add To Cart <svg viewBox="0 0 12 12"><path d="M2 2l4 4-4 4M6 2l4 4-4 4" fill="none" stroke="#fff" stroke-width="1.3"/></svg></a>
  </article>
  <article class="card" style="left:804px">
    <div class="thumb" role="img" aria-label="Hand holding a painted hook against snowy mountains" style="background:linear-gradient(180deg,#dce6da 0%,#e6eef4 20%,#9db4c8 60%,#eef1f3 85%,#dce6da)"></div>
    <h3>Painted Rose &amp; Ember Hook</h3>
    <div class="price">$165.00</div>
    <div class="rate"><svg width="18" height="16" viewBox="0 0 16 14"><path d="M8 14L1.5 7.5a3.8 3.8 0 016.5-4 3.8 3.8 0 016.5 4z" fill="var(--heart)"/></svg><svg width="58" height="11" viewBox="0 0 60 11" fill="var(--star)"><use href="#s"/><use href="#s" x="12"/><use href="#s" x="24"/><use href="#s" x="36"/><use href="#s" x="48"/></svg></div>
    <a class="btn" href="#">Add To Cart <svg viewBox="0 0 12 12"><path d="M2 2l4 4-4 4M6 2l4 4-4 4" fill="none" stroke="#fff" stroke-width="1.3"/></svg></a>
  </article>
</section>

<section class="explore">
  <h2 class="serif">Explore the trees<br>with me</h2>
  <p>Different trees are like personalities, they all have their unique qualities. I thought I would share some of them with you here, in the hopes of helping you decide which wood fits your needs best. But also, I love trees and I'm happy to introduce you to some of these lovely creatures that are apart of my craft and landscape. All of these trees are cut seasonally during trimming, and sometimes we get exotic cuts from rosemary, avocado, Persian lilac, and the like.</p>
  <a class="btn" href="#" style="left:110px;top:388px;width:137px;height:37px">Read More <svg viewBox="0 0 12 12"><path d="M2 2l4 4-4 4M6 2l4 4-4 4" fill="none" stroke="#fff" stroke-width="1.3"/></svg></a>
</section>
<div class="photo" role="img" aria-label="Live oak draped in moss" style="left:598px;top:2462px;width:326px;height:472px;background:linear-gradient(170deg,#c9cdc6,#6a6e58 40%,#3c3f2e 75%,#8a8e80)"></div>
<div class="photo" role="img" aria-label="Rustic carved hooks with dried orange slices on dark wood" style="left:924px;top:2462px;width:276px;height:472px;background:linear-gradient(170deg,#1e1c18,#3a2e22 40%,#8a6a3a 60%,#1c1a16)"></div>

<section class="seen">
  <h2 class="serif">As Seen In</h2>
  <div class="badge" style="left:128px"></div>
  <div class="badge" style="left:340px"></div>
  <div class="badge" style="left:520px"></div>
  <div class="badge" style="left:745px"></div>
  <div class="badge" style="left:950px"></div>
</section>

<section class="banner" role="img" aria-label="Row of hand-painted carved crochet hooks">
  <div class="plate">Moss River Twine</div>
</section>

<section class="follow">
  <div class="abs eyebrow" style="left:460px;top:3650px">
    <span class="script">Pictogram</span><span class="rule" style="width:100px"></span><span class="ornament" role="img" aria-label="Leaf ornament"></span>
  </div>
  <h2 class="serif">Follow Me</h2>
  <div class="photo" role="img" aria-label="Hooks in glass vases before a painted canvas" style="left:207px;top:3800px;width:225px;height:297px;background:linear-gradient(160deg,#4a6a8a,#b07a3a 50%,#5a3a2a)"></div>
  <div class="photo" role="img" aria-label="Carved earrings, black and white" style="left:207px;top:4108px;width:225px;height:232px;background:linear-gradient(160deg,#d8d8d8,#5a5a5a 50%,#2a2a2a)"></div>
  <div class="photo" role="img" aria-label="Painted hook on a cut wood round" style="left:445px;top:3800px;width:172px;height:185px;background:linear-gradient(160deg,#d8c8a8,#8a6a48)"></div>
  <div class="photo" role="img" aria-label="Hand holding carved earrings" style="left:624px;top:3800px;width:131px;height:185px;background:linear-gradient(160deg,#f2efe8,#c8a890 60%,#3a2a22)"></div>
  <div class="photo" role="img" aria-label="Painted hooks on a wooden board" style="left:445px;top:3994px;width:172px;height:176px;background:linear-gradient(160deg,#2a2418,#a8402a 50%,#3a2e22)"></div>
  <div class="photo" role="img" aria-label="Hooks beside a painted canvas" style="left:624px;top:3994px;width:131px;height:176px;background:linear-gradient(160deg,#5a4a3a,#a83a3a 50%,#e8e0d8)"></div>
  <div class="photo" role="img" aria-label="Yarn and hooks in a basket" style="left:445px;top:4180px;width:172px;height:160px;background:linear-gradient(160deg,#6a4a3a,#b8a0c8 50%,#4a3a2a)"></div>
  <div class="photo" role="img" aria-label="Carved hooks lined on dark fabric" style="left:634px;top:4180px;width:121px;height:160px;background:linear-gradient(90deg,#1c1c1c,#a89070 50%,#1c1c1c)"></div>
  <div class="photo" role="img" aria-label="Skein of grey yarn with dried flowers" style="left:766px;top:3800px;width:225px;height:293px;background:linear-gradient(160deg,#f4f4f2,#9aa4a8 50%,#5a6070)"></div>
  <div class="photo" role="img" aria-label="Row of round pendant stitch markers" style="left:766px;top:4108px;width:225px;height:232px;background:linear-gradient(180deg,#f4f2ee 30%,#c88a6a 55%,#f4f2ee 80%)"></div>
</section>

<footer class="site-footer">
  <div class="f-brand">mossrivertwine</div>
  <div class="f-dot"></div>
  <div class="news">Join Our Newsletter</div>
  <div class="field">Enter Email Address</div>
  <div class="sub">Subscribe Now</div>
  <div class="f-col" style="left:540px">
    <h4>Quick Links</h4>
    <a href="#">About Wren</a><a href="#">Feedback &amp; Reviews</a><a href="#">Look-Book Gallery</a><a href="#">Get In Touch</a><a href="#">Wood Types</a><a href="#">Art Hooks</a><a href="#">Rustic Hooks</a><a href="#">Custom Hooks</a>
  </div>
  <div class="f-col" style="left:757px">
    <h4>Account Details</h4>
    <a href="#">Shop</a><a href="#">Cart</a><a href="#">Checkout</a><a href="#">Account</a>
  </div>
  <div class="f-col" style="left:990px">
    <h4>Follow Us</h4>
    <a href="#"><span class="sq"></span>Threadbook</a><a href="#"><span class="sq"></span>Pictogram</a><a href="#"><span class="sq"></span>Pinboard</a>
  </div>
  <div class="line"></div>
  <div class="copy">Copyright © 2024 Moss River Twine - All rights reserved.</div>
</footer>

</body>
</html>
```